Artificial Intelligence Software Product Microsite

We specialises in Artificial Intelligence (AI) technology for big data analytics and we have a new product to be launched and requires a product microsite for it. Our product is an AI-driven Predictive/Prescriptive Analytics Engine that does the job of a Data Scientist or a group of Data Scientists, highly intelligent and fully automated, where endusers do not require any machine-learning knowledge. We would like to see a design that's simple yet futuristic and provide an impression that it is highly technological advanced. Key messages to deliver are that it is first of its kind in the world, it deploys state-of-the-art technology, a solution that is easy to adopt and integrate into their existing or planned apps. It is in effect a (or a pool of) Virtual Data Scientist(s) at their disposal that will work for them tirelessly 365 days a year and at a small fraction of the cost of a data scientist. Will provide more details, files/images only to shortlisted designers. Expecting something that is simple and straightforward that sufficiently showcase the product/technology.

Deadline will be extended if necessary to facilitate shortlisted designers.
Updates

Reason: To provide designers with more time for submission and amendments. For those who have not submitted your design, pls do so ASAP and also submit your concept first. Pls ensure that you are designing a Product Micro-site and not a corporate website. It's meant to introduce the product only, not the company. Only an enquiry email address is to be included at the bottom. Already said in my earlier public comments, would want something that is scroll-down to view more info rather then having to click to view different pages. This is a pre-requisite as stated both in my project brief and public comments. Thank you for participating and looking forward to see something really good soon.

Target Market(s)

App Developers in the Software Industry or any Enterprise Customers with in-house apps.

Industry/Entity Type

Computer Software

Coding

Coded - Design and coding required

Number of Pages Required

3 page

Font styles to use
Other font styles liked:
• Pls refer to attachments.

Requirements
Must have
• Please refer to the attached document "BrambleAI 1-page Infosheet". Key message to be delivered is as per this document but need to add in additional information on performance comparisons, which is a small section but only ready on 10th Jul. The microsite doesn't have to be strictly 3 pages but can be less or more if necessary but do go along the lines of the modern sites whereby when options are clicked, the page slides down to the specific option selected instead. Prefers some simple animation, especially for the diagram that depicts the high-level architecture of our AI engine, how the process flows between the different components. Make it simple yet futuristic. The key theme or focal point is "Virtual Data Scientist". Would like to see something that's short and straight to the point, with a clean design.
Nice to have
• If you can use suitable images of a (or group of) human data scientist(s) depicting the transformation to a "Virtual Data Scientist" will be great.
Should not have
• This is a software technology to be introduced and as such, must have a design or theme appropriate for the industry. It should not have the kind of generic look-and-feel that other industries uses.

```html
<!DOCTYPE html>
<html lang="en">
<head>
<meta charset="utf-8">
<title>BrambleAI – Virtual Data Scientist</title>
<link href="https://fonts.googleapis.com/css2?family=Open+Sans:wght@300;400;600;700&display=swap" rel="stylesheet">
<style>
:root{
  --red:#e2313b;
  --red-dark:#c92730;
  --ink:#2b2b2b;
  --charcoal:#363636;
  --charcoal-2:#2d2d2d;
  --slate:#3c3c3c;
  --grey:#777;
  --light:#f4f4f4;
  --white:#fff;
  --footer:#1f1f1f;
}
*{margin:0;padding:0;box-sizing:border-box}
html,body{width:736px;height:1200px;overflow:hidden}
body{font-family:"Open Sans",Arial,sans-serif;color:var(--ink);background:var(--white);position:relative}
.abs{position:absolute}

/* header */
.site-header{left:0;top:0;width:736px;height:55px;background:var(--white)}
.brand{left:22px;top:14px;display:flex;align-items:center;gap:7px;font-weight:700;font-size:20px;color:var(--ink);letter-spacing:.3px}
.brand-mark{width:12px;height:12px;background:var(--red)}
.main-nav{left:290px;top:30px;display:flex;gap:16px;font-size:7px;font-weight:600;color:var(--ink);letter-spacing:.4px;white-space:nowrap}
.social{left:545px;top:27px;display:flex;gap:5px}
.social span{width:13px;height:13px;border-radius:50%;background:var(--charcoal)}
.account-links{left:662px;top:10px;font-size:7px;line-height:12px;color:var(--grey);text-align:left}
.header-rule{left:0;top:55px;width:736px;height:4px;background:var(--red)}

/* hero */
.hero{left:0;top:59px;width:736px;height:309px;background:linear-gradient(180deg,var(--charcoal) 0%,var(--charcoal-2) 100%);color:var(--white);text-align:center}
.hero h1{position:absolute;left:0;width:736px;top:48px;font-weight:300;font-size:34px;letter-spacing:1px}
.hero .tagline{position:absolute;left:0;width:736px;top:92px;font-size:14px;font-weight:300}
.step{position:absolute;top:128px;width:140px;text-align:center}
.step .disc{width:108px;height:108px;border-radius:50%;margin:0 auto;border:5px solid var(--white);display:flex;align-items:center;justify-content:center}
.step .disc.red{background:var(--red)}
.step .disc.white{background:var(--white);border-color:var(--red)}
.step .art{width:60px;height:60px;border-radius:50%}
.step .disc.red .art{background:radial-gradient(circle,#f3f3f3 0%,#bfbfbf 100%)}
.step .disc.white .art{background:radial-gradient(circle,#cfcfcf 0%,#8a8a8a 100%)}
.step h3{margin-top:14px;font-size:13px;font-weight:600;letter-spacing:.6px}

/* for what */
.features{left:0;top:368px;width:736px;height:270px;background:var(--white)}
.features .illustration{position:absolute;left:52px;top:54px;width:128px;height:116px;background:linear-gradient(160deg,#dfe6ec 0%,#9fb2c0 100%);border-radius:4px}
.section-title{font-size:27px;font-weight:400;color:var(--red)}
.features .section-title{position:absolute;left:343px;top:40px}
.features .lead{position:absolute;left:343px;top:80px;font-size:10px;color:var(--grey)}
.feature-col{position:absolute;top:104px;width:170px}
.feature-col li{list-style:none;margin-bottom:14px;font-size:8px;color:var(--grey);line-height:11px;padding-left:10px;position:relative}
.feature-col li::before{content:"";position:absolute;left:0;top:4px;width:4px;height:4px;border-radius:50%;background:var(--ink)}
.feature-col strong{display:block;font-size:10px;color:var(--ink);font-weight:600;margin-bottom:2px}

/* audience */
.audience{top:650px;width:368px;height:198px;color:var(--white)}
.audience.whom{left:0;background:var(--red)}
.audience.why{left:368px;background:var(--slate)}
.audience .section-title{position:absolute;left:48px;top:28px;color:var(--white)}
.audience .intro{position:absolute;left:48px;top:68px;width:240px;font-size:9px;line-height:12px;opacity:.9}
.audience ul{position:absolute;left:62px;top:104px;width:280px}
.audience li{list-style:none;font-size:8px;line-height:11px;margin-bottom:8px;padding-left:10px;position:relative;opacity:.92}
.audience li::before{content:"";position:absolute;left:0;top:4px;width:4px;height:4px;border-radius:50%;background:var(--white)}
.audience li strong{display:block;font-size:10px;font-weight:600}

/* use cases */
.use-cases{left:0;top:848px;width:736px;height:267px;background:var(--white)}
.use-cases .section-title{position:absolute;left:46px;top:26px;font-size:29px}
.use-cases .lead{position:absolute;left:46px;top:68px;font-size:10px;color:var(--grey)}
.use-cases ul{position:absolute;left:62px;top:94px}
.use-cases li{list-style:none;font-size:8px;color:var(--grey);line-height:15px;padding-left:12px;position:relative}
.use-cases li::before{content:"";position:absolute;left:0;top:5px;width:5px;height:5px;background:var(--ink)}
.use-cases .photo{position:absolute;left:440px;top:6px;width:268px;height:256px;background:linear-gradient(200deg,#f2f2f2 0%,#d8d8d8 55%,#9e9e9e 100%);border-radius:4px}

/* footer */
.site-footer{left:0;top:1115px;width:736px;height:85px;background:var(--footer);color:#bbb}
.footer-block{position:absolute;top:22px;font-size:8px;line-height:12px}
.footer-block h4{color:var(--white);font-size:10px;font-weight:600;letter-spacing:.5px;margin-bottom:3px}
.follow{position:absolute;left:470px;top:30px;display:flex;align-items:center;gap:8px;color:var(--white);font-size:11px;font-weight:600;letter-spacing:.6px}
.follow span{width:15px;height:15px;border-radius:3px;background:#d9d9d9}
.page-no{position:absolute;left:698px;top:32px;font-size:8px;color:#999}
</style>
</head>
<body>

<header class="site-header abs">
  <div class="brand abs"><span class="brand-mark"></span>BrambleAI</div>
  <nav class="main-nav abs"><span>HOME</span><span>ABOUT US</span><span>PRODUCTS</span><span>MEMBERS</span><span>BLOG</span></nav>
  <div class="social abs"><span></span><span></span><span></span><span></span></div>
  <div class="account-links abs">Sign In<br>Join<br>Contact Us</div>
</header>
<div class="header-rule abs"></div>

<section class="hero abs">
  <h1>VIRTUAL&nbsp; DATA SCIENTIST</h1>
  <p class="tagline">For App Developers</p>
  <div class="step" style="left:90px">
    <div class="disc red"><div class="art" role="img" aria-label="Tablet collecting data"></div></div>
    <h3>GATHER IT</h3>
  </div>
  <div class="step" style="left:298px">
    <div class="disc white"><div class="art" role="img" aria-label="Cloud storage"></div></div>
    <h3>STORE IT</h3>
  </div>
  <div class="step" style="left:506px">
    <div class="disc white"><div class="art" role="img" aria-label="Devices showing learned insights"></div></div>
    <h3>LEARN FROM IT</h3>
  </div>
</section>

<section class="features abs">
  <div class="illustration" role="img" aria-label="Monitor with analytics charts and a magnifying glass"></div>
  <h2 class="section-title">For What</h2>
  <p class="lead">Driven by advanced AI</p>
  <ul class="feature-col" style="left:350px">
    <li><strong>Easy to Adopt</strong>No machine-learning knowledge is required</li>
    <li><strong>Intelligent</strong>Self-modeling, selection and optimisation of algorithms and ability to handle incomplete data</li>
  </ul>
  <ul class="feature-col" style="left:550px">
    <li><strong>Lightweight</strong>Runs even on small edge devices</li>
    <li><strong>Self-Learning</strong>Learns from every new data stream for faster and more precise predictions</li>
  </ul>
</section>

<section class="audience whom abs">
  <h2 class="section-title">For Whom</h2>
  <p class="intro">The BrambleAI big data analytics engine can be adopted by any :</p>
  <ul>
    <li><strong>Devs</strong>for faster productising of enhancements</li>
    <li><strong>Enterprise Users</strong>for enabling their in-house apps with customised predictive analytics for their own organisation</li>
  </ul>
</section>
<section class="audience why abs">
  <h2 class="section-title">And Why</h2>
  <p class="intro">The BrambleAI big data analytics engine can be adopted by any :</p>
  <ul>
    <li><strong>Data Analysis and Discovery</strong>providing historical and untapped insights</li>
    <li><strong>Predictions</strong>providing insights into the future</li>
  </ul>
</section>

<section class="use-cases abs">
  <h2 class="section-title">USE CASES</h2>
  <p class="lead">Big Data analytics that include</p>
  <ul>
    <li>Business Analytics</li>
    <li>Fraud or Anomaly detection</li>
    <li>Trading Analytics and Predictions</li>
    <li>Monitoring and analysis of IoT devices</li>
    <li>Sales/Marketing Research and Directions</li>
    <li>Social Media Analytics</li>
    <li>Sports Performance Analytics and Results Predictions</li>
    <li>User experience enhancements and application process automation</li>
  </ul>
  <div class="photo" role="img" aria-label="Hand holding a tablet with a rising bar chart"></div>
</section>

<footer class="site-footer abs">
  <div class="footer-block" style="left:46px"><h4>COPYRIGHT</h4>© 2016 BrambleAI. All rights reserved.</div>
  <div class="footer-block" style="left:290px"><h4>ADDRESS</h4>hello@brambleai.com</div>
  <div class="follow">FOLLOW US <span></span><span></span><span></span><span></span><span></span></div>
  <div class="page-no">17</div>
</footer>

</body>
</html>
```